International oil and gas consultancy business needs a web design

Hello, I need a web design for a new oil and gas auditing consultancy business. My business undertakes contract audit assignments to review past costs of oil and gas operations (see attached Excel file for more details of the businesses services). I need the design to give the impression of a professional consultancy style of business, rather than a retail style of website. Note: this job is for LAYOUT DESIGN ONLY and not coding / development work.
The following are my key design principles:
1. BASIC DESIGN: I am after a simple and static web design. I don't want the pages busy or cluttered with too many images or detail.
2. HORIZONTAL TABS: I require a horizontal set of tabs towards the top of the screens (see Excel file) which remain in the same position on every page.
3. META TAG PLANNING: The design should allow for effective positioning of content so that key meta tag words can easily be built during the technical build stage.
4. NUMBER OF PAGES: The site will eventually have a maximum of 10 pages. Seven of the pages will reside under the tabs. Can you please present your opening submission for the first two page.
5. USE OF MY LOGO: The attached logo (JPEG file) should be used throughout the website. Please don't change the shape and colour.
6. COLOUR SCHEMES: Can you please consider any of the 3 colour schemes below:
A - dark red (to match the logo), light grey and perhaps another of your liking;
B - dark red (to match the logo), light cream and perhaps another of your liking;
C - dark red (to match the logo), white and perhaps another of your liking.
7. WORD CONTENT: I have attached an Excel file which shows the estimated word content for each page.
8. FUTURE USE OF DESIGN: I'm planning on building a Wordpress website. Can you please ensure the layout design supports this application.

Target Market(s)

oil and gas companies (small and large)

Industry/Entity Type

Oil And Gas

Font styles to use
Sans Serif

Requirements
Nice to have
• The KRL logo and business name should ideally be next to each other. Also, the logo and name should be part of the background graphics, not above it.

```html
<!DOCTYPE html>
<html lang="en">
<head>
<meta charset="utf-8">
<title>KRL – Oil and Gas Auditing</title>
<link rel="stylesheet" href="https://fonts.googleapis.com/css2?family=Nunito+Sans:wght@300;400;600&display=swap">
<style>
:root{
  --red:#8e1b1f;
  --red-dark:#6f1215;
  --ink:#444;
  --muted:#555;
  --rule:#d9d9d9;
  --btn:#e9e9e9;
  --foot:#eeeeee;
  --white:#fff;
}
*{box-sizing:border-box;margin:0;padding:0}
html,body{width:1200px;height:1070px;overflow:hidden;background:var(--white)}
body{font-family:"Nunito Sans",Arial,sans-serif;color:var(--ink);position:relative}
.brand{position:absolute;left:77px;top:18px;font-size:54px;font-weight:600;color:var(--red);letter-spacing:2px;line-height:1}
.nav{position:absolute;top:64px;left:0;width:1200px;height:20px}
.nav a{position:absolute;font-size:13.5px;color:var(--ink);text-decoration:none;letter-spacing:.3px;white-space:nowrap}
.nav a.active{color:var(--red)}
.hero{position:absolute;left:74px;top:98px;width:1052px;height:456px;overflow:hidden}
.hero-photo{position:absolute;inset:0;background:
  radial-gradient(ellipse at 42% 78%,#f6a21a 0%,#e0701f 22%,#a4442a 48%,#5b2d2e 75%,#2e2024 100%)}
.hero-copy{position:absolute;left:558px;top:115px;width:470px;color:var(--white)}
.hero-copy h1{font-size:37px;font-weight:400;line-height:1.1;margin-bottom:6px}
.hero-copy p{font-size:16.6px;line-height:23px;font-weight:400}
.hero-copy .more{margin-top:21px}
.dots{position:absolute;left:499px;top:424px;display:flex;gap:7px}
.dots span{width:11px;height:11px;border-radius:50%;background:#9a9a9a}
.dots span.on{background:var(--white)}
.more{display:flex;width:138px;height:30px}
.more .label{flex:1;background:var(--btn);color:var(--red);font-size:13px;display:flex;align-items:center;padding-left:15px;letter-spacing:.2px}
.more .arrow{width:28px;background:var(--red);display:flex;align-items:center;justify-content:center}
.services{position:absolute;top:598px;left:0;width:1200px}
.service{position:absolute;height:55px;width:330px;background:var(--red);border-bottom:3px solid var(--red-dark);color:var(--white);font-size:18.5px;letter-spacing:.6px;display:flex;align-items:center;justify-content:space-between;padding:0 15px 0 17px;word-spacing:3px}
.rule{position:absolute;top:695px;height:1px;background:var(--rule)}
.who-photo{position:absolute;left:74px;top:726px;width:270px;height:180px;background:linear-gradient(135deg,#d9dde3 0%,#f3f3f1 45%,#e9a15c 80%,#d2742c 100%)}
.section-title{font-size:19px;font-weight:400;color:var(--red);letter-spacing:.3px}
.who{position:absolute;left:369px;top:722px;width:490px}
.who p{margin-top:11px;font-size:12.5px;line-height:21.2px;color:var(--muted);font-weight:400}
.who .more{position:absolute;top:155px}
.why{position:absolute;left:884px;top:722px;width:250px}
.why ul{list-style:none;margin-top:11px}
.why li{font-size:12.5px;line-height:28.6px;color:var(--muted);padding-left:22px;position:relative;margin-top:-7px}
.why li:first-child{margin-top:0}
.why li::before{content:"";position:absolute;left:1px;top:12px;width:5px;height:5px;border-radius:50%;background:var(--red)}
.why .more{position:absolute;top:155px}
.footer{position:absolute;left:0;top:947px;width:1200px;height:123px;background:var(--foot)}
.footer .brand-small{position:absolute;left:75px;top:22px;font-size:30px;font-weight:600;color:#777;letter-spacing:1px;line-height:1}
.footer .legal{position:absolute;left:75px;top:68px;font-size:13px;line-height:17px;color:var(--muted)}
.footer .legal em{font-style:normal;color:var(--red)}
.connect{position:absolute;left:1025px;top:12px;font-size:15px;color:var(--red)}
.social{position:absolute;left:1025px;top:42px;display:flex;gap:5px}
.social span{width:30px;height:30px;border-radius:50%;background:var(--red)}
</style>
</head>
<body>
<header>
  <div class="brand">KRL</div>
  <nav class="nav">
    <a class="active" style="left:346px">HOME</a>
    <a style="left:426px">ABOUT US</a>
    <a style="left:534px">SERVICES</a>
    <a style="left:637px">OUR PARTNERS</a>
    <a style="left:777px">APPROACH</a>
    <a style="left:891px">WHY CHOOSE US</a>
    <a style="left:1042px">CONTACT US</a>
  </nav>
</header>

<section class="hero">
  <div class="hero-photo" role="img" aria-label="Silhouettes of two engineers in hard hats shaking hands before an offshore oil platform at sunset"></div>
  <div class="hero-copy">
    <h1>Kestrel Ridge Auditing</h1>
    <p>is a Perth (Australia) based firm specialising in providing quality audit services for the oil and gas industry. Our skills and knowledge of oil and gas, along with a deep understanding of business commercial needs, ensures the high quality of our services...</p>
    <div class="more"><span class="label">LEARN MORE</span><span class="arrow"><svg width="8" height="12" viewBox="0 0 8 12"><path d="M1.5 1l5 5-5 5" fill="none" stroke="#fff" stroke-width="2"/></svg></span></div>
  </div>
  <div class="dots"><span class="on"></span><span></span><span></span><span></span></div>
</section>

<section class="services">
  <div class="service" style="left:74px">JOINT VENTURE AUDITS<svg width="18" height="18" viewBox="0 0 18 18"><circle cx="9" cy="9" r="9" fill="#fff"/><path d="M7 5l5 4-5 4z" fill="#8e1b1f"/></svg></div>
  <div class="service" style="left:436px">CONTRACT AUDITS<svg width="18" height="18" viewBox="0 0 18 18"><circle cx="9" cy="9" r="9" fill="#fff"/><path d="M7 5l5 4-5 4z" fill="#8e1b1f"/></svg></div>
  <div class="service" style="left:796px">OPERATIONS AUDITS<svg width="18" height="18" viewBox="0 0 18 18"><circle cx="9" cy="9" r="9" fill="#fff"/><path d="M7 5l5 4-5 4z" fill="#8e1b1f"/></svg></div>
</section>

<div class="rule" style="left:74px;width:783px"></div>
<div class="rule" style="left:884px;width:242px"></div>

<main>
  <div class="who-photo" role="img" aria-label="Hands working with a pen and calculator over financial charts beside a laptop"></div>
  <section class="who">
    <h2 class="section-title">WHO WE ARE</h2>
    <p>Kestrel Ridge Auditing, trading as Kestrel Ridge Auditing Pty Ltd, is incorporated and based in Perth, Western Australia. The firm was founded in 2014 by Sam Porter. Sam has over 20 years of diverse accounting, project and operational experience. Starting out as an auditor in public practice, Sam moved into commerce and held CFO, COO and many EPC project (construction) finance positions.</p>
    <div class="more"><span class="label">LEARN MORE</span><span class="arrow"><svg width="8" height="12" viewBox="0 0 8 12"><path d="M1.5 1l5 5-5 5" fill="none" stroke="#fff" stroke-width="2"/></svg></span></div>
  </section>
  <section class="why">
    <h2 class="section-title">WHY CHOOSE US</h2>
    <ul>
      <li>Cost savings</li>
      <li>Risk Mitigation</li>
      <li>Process Improvement</li>
      <li>Contractual Efficiency &amp; Effectiveness</li>
    </ul>
    <div class="more"><span class="label">LEARN MORE</span><span class="arrow"><svg width="8" height="12" viewBox="0 0 8 12"><path d="M1.5 1l5 5-5 5" fill="none" stroke="#fff" stroke-width="2"/></svg></span></div>
  </section>
</main>

<footer class="footer">
  <div class="brand-small">KRL</div>
  <div class="legal">Copyright © 2014 <em>KRL</em><br>Site Map / Terms and Conditions / Privacy Policy</div>
  <div class="connect">Connect Us</div>
  <div class="social" aria-label="Social links"><span></span><span></span><span></span></div>
</footer>
</body>
</html>
```